Real Estate Company
Residential & Commercial
Sales & Property Management

would like to use the logo i uploaded but would really love a black back ground...I think with the gold fleur dis lis and the maroon lettering it would really look great!

Industry/Entity Type

Business

Contact Information for Business Card

Our Coastal Real Estate Co.
Danielle Forbis
Broker/Owner
337-284-6093 Cell
337-726-0348 Office
8142 Willet Rd Pelican Bay LA 70612

```html
<!DOCTYPE html>
<html lang="en">
<head>
<meta charset="utf-8">
<title>Our Coastal Real Estate Co. – Business Card</title>
<link rel="stylesheet" href="https://fonts.googleapis.com/css2?family=Cinzel:wght@400;600&display=swap">
<style>
  :root {
    --backdrop: #141414;
    --card-black: #050505;
    --gold-light: #f3e3a0;
    --gold-mid: #c9a542;
    --gold-dark: #8e6f1f;
    --maroon: #8c2a2e;
    --accent-yellow: #e8d23a;
  }
  * { margin: 0; padding: 0; box-sizing: border-box; }
  html, body {
    width: 1200px; height: 871px; overflow: hidden;
    background: var(--backdrop);
    font-family: "Cinzel", "Times New Roman", serif;
  }
  .canvas { position: relative; width: 1200px; height: 871px; }

  .card {
    position: absolute;
    width: 540px; height: 309px;
    padding: 14px;
    background: linear-gradient(135deg, var(--gold-light) 0%, var(--gold-mid) 35%, var(--gold-dark) 60%, var(--gold-mid) 80%, var(--gold-light) 100%);
  }
  .card__face {
    position: relative;
    width: 100%; height: 100%;
    background: var(--card-black);
  }
  .card--back { left: 70px; top: 110px; }
  .card--front { left: 590px; top: 452px; }

  .wordmark {
    position: absolute;
    display: flex; align-items: center; gap: 12px;
    color: var(--maroon);
    font-weight: 600;
    line-height: 1.05;
  }
  .wordmark__dot {
    flex: none;
    width: 22px; height: 22px; border-radius: 50%;
    background: var(--gold-mid);
  }
  .card--back .wordmark { left: 0; right: 0; top: 0; bottom: 0; justify-content: center; font-size: 30px; }
  .card--front .wordmark { right: 24px; top: 44px; width: 240px; font-size: 23px; }

  .contact {
    position: absolute; left: 40px; top: 64px;
    width: 220px;
    color: var(--maroon);
    font-size: 11px; letter-spacing: 0.05em; text-transform: uppercase;
  }
  .contact__name { font-size: 15px; letter-spacing: 0.1em; }
  .contact__title { color: var(--accent-yellow); font-size: 9.5px; font-weight: 600; margin-bottom: 18px; }
  .contact__address { line-height: 1.5; margin-bottom: 10px; }
  .contact__line { display: flex; align-items: center; gap: 8px; line-height: 1.7; }
  .contact__icon { width: 12px; height: 12px; flex: none; }
</style>
</head>
<body>
<main class="canvas">
  <section class="card card--back" aria-label="Card back">
    <div class="card__face">
      <div class="wordmark"><span class="wordmark__dot"></span><span>Our Coastal<br>Real Estate Co.</span></div>
    </div>
  </section>

  <section class="card card--front" aria-label="Card front">
    <div class="card__face">
      <div class="contact">
        <p class="contact__name">Danielle Forbis</p>
        <p class="contact__title">Broker/Owner</p>
        <p class="contact__address">Office 8142<br>Willet Rd Pelican Bay LA 70612</p>
        <p class="contact__line">
          <svg class="contact__icon" viewBox="0 0 12 12" aria-hidden="true"><path d="M1 4c0-2 2-3 5-3s5 1 5 3l-2 1-1-2H4L3 5 1 4zM3 6h6l1 5H2z" fill="var(--accent-yellow)"/></svg>
          <span>337-284-6093</span>
        </p>
        <p class="contact__line">
          <svg class="contact__icon" viewBox="0 0 12 12" aria-hidden="true"><rect x="3" y="0.5" width="6" height="11" rx="1.2" fill="none" stroke="var(--accent-yellow)" stroke-width="1.2"/><rect x="4.3" y="2" width="3.4" height="5" fill="var(--accent-yellow)"/></svg>
          <span>Cell 337-726-0348</span>
        </p>
      </div>
      <div class="wordmark"><span class="wordmark__dot"></span><span>Our Coastal<br>Real Estate Co.</span></div>
    </div>
  </section>
</main>
</body>
</html>
```